Single-sided business card for restaurant velmora with new logo made on this site

Business card options with new logo including restaurant name, address, phone number and website. This business card is single-sided only and will be presented at the hostess desk for clients to take. I would like to see options based on a cream card background, a white card background, a yellow card background and a burgundy colored background. It needs to be elegant and traditional.

Target Market(s)

local and international crowd

Industry/Entity Type

restaurant

Contact Information for Business Card

address, website and phone number

Font styles to use
Serif

Colors
EE7325
F08F49
F5BC92
FAE3D3
FDF4ED

Requirements
Must have
• new logo, address, phone number, website
Should not have
• more than three colors

```html
<!DOCTYPE html>
<html lang="es">
<head>
<meta charset="utf-8">
<title>Velmora – Tarjeta de presentación</title>
<link rel="stylesheet" href="https://fonts.googleapis.com/css2?family=Cinzel:wght@400;500&family=Arimo:wght@400&display=swap">
<style>
  :root {
    --backdrop: #e9e6e2;
    --card: #ffffff;
    --gold: #f5b430;
    --ink: #3a1a14;
  }
  * { margin: 0; padding: 0; box-sizing: border-box; }
  html, body {
    width: 1200px;
    height: 900px;
    overflow: hidden;
    background: var(--backdrop);
  }
  .business-card {
    position: absolute;
    left: 100px;
    top: 160px;
    width: 1000px;
    height: 580px;
    background: var(--card);
    color: var(--ink);
  }
  .brand {
    position: absolute;
    left: 0;
    right: 0;
    top: 58px;
    display: flex;
    flex-direction: column;
    align-items: center;
  }
  .brand-square {
    width: 170px;
    height: 170px;
    background: var(--gold);
  }
  .brand-name {
    margin-top: 22px;
    font-family: "Cinzel", serif;
    font-weight: 500;
    font-size: 60px;
    letter-spacing: 0.16em;
    line-height: 1;
    color: var(--ink);
  }
  .reservation-band {
    position: absolute;
    left: 0;
    right: 0;
    top: 366px;
    height: 50px;
    background: var(--gold);
    display: flex;
    align-items: center;
    padding-left: 300px;
  }
  .reservation-line {
    font-family: "Cinzel", serif;
    font-weight: 500;
    font-size: 34px;
    letter-spacing: 0.02em;
    color: var(--ink);
  }
  .address {
    position: absolute;
    left: 200px;
    top: 446px;
    font-family: "Arimo", sans-serif;
    font-size: 25px;
    line-height: 1.3;
    font-style: normal;
    color: var(--ink);
  }
  .website {
    position: absolute;
    right: 70px;
    top: 446px;
    font-family: "Arimo", sans-serif;
    font-size: 25px;
    color: var(--ink);
  }
</style>
</head>
<body>
  <article class="business-card">
    <header class="brand">
      <div class="brand-square"></div>
      <h1 class="brand-name">VELMORA</h1>
    </header>
    <div class="reservation-band">
      <p class="reservation-line">RESERVACIONES 958-412-3076</p>
    </div>
    <address class="address">
      Restaurant Velmora,<br>
      Jazmín 418, Bahías de Huatulco,<br>
      Oaxaca CP 70989
    </address>
    <p class="website">www.velmora.com.mx</p>
  </article>
</body>
</html>
```